BRIGHT RIVER POWER.

I'd like my business logo.
contact name: Dennis Halvorsen
phone:0438759164
email: info@brightriverpower.net.au
website: www.brightriverpower.net.au

services:
solar
battery storage
LED lighting
energy saving solutions
general electrical
I'd like the design to look professional

Target Market(s)

Everyone

Industry/Entity Type

Business

Contact Information for Business Card

as described above

Requirements
Must have
• Id like the colours and the design to work well with my logo.

```html
<!DOCTYPE html>
<html lang="en">
<head>
<meta charset="utf-8">
<title>Bright River Power – Business Card</title>
<link rel="stylesheet" href="https://fonts.googleapis.com/css2?family=Lato:wght@400;700&display=swap">
<style>
  :root {
    --backdrop: #a9adb2;
    --card: #ffffff;
    --brand-green: #4cae4f;
    --service-green: #3a9e5a;
    --ink: #4d4d4d;
    --ink-soft: #3f3f3f;
    --rule: #8a8a8a;
  }
  * { margin: 0; padding: 0; box-sizing: border-box; }
  html, body {
    width: 1200px;
    height: 1000px;
    overflow: hidden;
    background: var(--backdrop);
    font-family: "Lato", Arial, sans-serif;
  }
  .business-card {
    position: absolute;
    left: 100px;
    top: 210px;
    width: 1000px;
    height: 580px;
    background: var(--card);
    box-shadow: 0 6px 18px rgba(0,0,0,0.18);
  }
  .brand-row {
    position: absolute;
    left: 56px;
    top: 70px;
    right: 56px;
    height: 120px;
    display: flex;
    align-items: center;
  }
  .brand-name {
    display: flex;
    align-items: center;
    gap: 16px;
    width: 440px;
    font-weight: 700;
    font-size: 36px;
    line-height: 1.05;
    color: var(--brand-green);
    letter-spacing: 1px;
  }
  .brand-dot {
    flex: none;
    width: 62px;
    height: 62px;
    border-radius: 50%;
    background: var(--brand-green);
  }
  .brand-divider {
    width: 2px;
    height: 96px;
    background: var(--brand-green);
    margin: 0 26px 0 0;
  }
  .service-list {
    list-style: none;
    color: var(--service-green);
    font-size: 21px;
    letter-spacing: 1.2px;
    line-height: 25px;
    text-transform: uppercase;
  }
  .card-rule {
    position: absolute;
    left: 56px;
    right: 56px;
    top: 212px;
    height: 1.5px;
    background: var(--rule);
  }
  .contact-name {
    position: absolute;
    left: 64px;
    top: 248px;
    font-size: 58px;
    font-weight: 700;
    color: var(--ink);
    letter-spacing: 1px;
  }
  .contact-list {
    position: absolute;
    left: 60px;
    top: 348px;
    list-style: none;
  }
  .contact-item {
    display: flex;
    align-items: center;
    height: 50px;
    margin-bottom: 2px;
    font-size: 26px;
    color: var(--ink-soft);
  }
  .contact-icon {
    width: 36px;
    height: 36px;
    margin-right: 16px;
    flex: none;
  }
</style>
</head>
<body>
  <article class="business-card">
    <header class="brand-row">
      <div class="brand-name">
        <span class="brand-dot"></span>
        <span>BRIGHT RIVER POWER</span>
      </div>
      <span class="brand-divider"></span>
      <ul class="service-list">
        <li>Solar</li>
        <li>Battery Storage</li>
        <li>LED Lighting</li>
        <li>Energy Saving Solutions</li>
      </ul>
    </header>

    <div class="card-rule"></div>

    <h1 class="contact-name">Dennis Halvorsen</h1>

    <ul class="contact-list">
      <li class="contact-item">
        <svg class="contact-icon" viewBox="0 0 36 36" aria-hidden="true">
          <rect x="3" y="9" width="30" height="19" rx="1" fill="var(--brand-green)"/>
          <path d="M3 9 L18 21 L33 9" fill="none" stroke="#fff" stroke-width="2"/>
        </svg>
        info@brightriverpower.net.au
      </li>
      <li class="contact-item">
        <svg class="contact-icon" viewBox="0 0 36 36" aria-hidden="true">
          <rect x="10" y="3" width="16" height="30" rx="3" fill="var(--brand-green)"/>
          <rect x="12.5" y="7" width="11" height="19" fill="#fff"/>
          <circle cx="18" cy="29.5" r="1.6" fill="#fff"/>
        </svg>
        0438 759 164
      </li>
      <li class="contact-item">
        <svg class="contact-icon" viewBox="0 0 36 36" aria-hidden="true">
          <circle cx="18" cy="18" r="15" fill="var(--brand-green)"/>
          <g fill="none" stroke="#fff" stroke-width="1.6">
            <ellipse cx="18" cy="18" rx="6.5" ry="15"/>
            <line x1="3" y1="18" x2="33" y2="18"/>
            <line x1="18" y1="3" x2="18" y2="33"/>
            <path d="M6 10 H30 M6 26 H30"/>
          </g>
        </svg>
        www.brightriverpower.net.au
      </li>
    </ul>
  </article>
</body>
</html>
```